Fresh, modern, fun business card for pediatric dental practice

Need a business card for fresh, modern, fun pediatric dental practice

Clean look that matches our website's font and colors

We prefer the look of curved corners on business cards

Target Market(s)

parents (mothers) of young children, professionals, mid-high class

Industry/Entity Type

Dental

Contact Information for Business Card

Maplebrook Pediatric Dentistry
482 Quarry Lane
Suite 517
Fernhollow, ST 00412
717.555.0193
www.maplebrookkidsdental.example

Mei-Ran Tsai, DMD
Corinne Walbeck, DMD
(we are working on our email address, but we would like that on the card as well)

Font styles to use
Sans Serif

Requirements
Must have
• All info; we would also like to make cards for individual staff members
• colors from our website and color palatte, attatched
• use same font and design as website for branding
Nice to have
• clean, simple card that has a pop of color
• we would like to see a few designs with our tag line "where smiles get brighter"
• we are not sure if we want to have it on there or not
• we would like to see a few designs incorporating the ribbon graphic on our website where the word WELCOME is

```html
<!DOCTYPE html>
<html lang="en">
<head>
<meta charset="utf-8">
<title>Maplebrook Pediatric Dentistry – Business Card</title>
<link rel="stylesheet" href="https://fonts.googleapis.com/css2?family=Open+Sans:wght@400;600&family=Roboto:wght@400;500&family=Roboto+Condensed:wght@500&display=swap">
<style>
  :root {
    --backdrop: #2b2b2b;
    --card: #f4f4f4;
    --sun: #f0b323;
    --berry: #c8308c;
    --ink: #4a4a4a;
    --white: #ffffff;
  }
  * { box-sizing: border-box; margin: 0; padding: 0; }
  html, body { width: 1200px; height: 960px; overflow: hidden; }
  body {
    background: var(--backdrop);
    font-family: "Roboto", Arial, sans-serif;
    position: relative;
  }
  .card {
    position: absolute;
    width: 600px;
    height: 342px;
    border-radius: 22px;
    background: var(--card);
    overflow: hidden;
  }
  .card--front { left: 314px; top: 113px; }
  .card--back { left: 311px; top: 472px; }

  .brand {
    position: absolute;
    top: 0; left: 0; right: 0;
    height: 204px;
    text-align: center;
    font-family: "Open Sans", Arial, sans-serif;
  }
  .brand__mark {
    display: block;
    width: 48px; height: 48px;
    border-radius: 50%;
    background: var(--sun);
    margin: 40px auto 16px;
  }
  .brand__name {
    color: var(--sun);
    font-weight: 600;
    font-size: 44px;
    line-height: 1;
    letter-spacing: 1.5px;
  }
  .brand__tag {
    color: var(--berry);
    font-weight: 400;
    font-size: 21px;
    line-height: 1.35;
    letter-spacing: 1.2px;
  }

  .doctors {
    position: absolute;
    top: 204px; left: 0; right: 0;
    height: 58px;
    background: var(--sun);
    color: var(--white);
    font-family: "Roboto Condensed", "Arial Narrow", sans-serif;
    font-weight: 500;
    font-size: 21px;
    line-height: 24px;
    text-align: center;
    padding-top: 5px;
  }
  .contact {
    position: absolute;
    top: 262px; left: 0; right: 0; bottom: 0;
    background: var(--berry);
    color: var(--white);
    font-size: 14.5px;
    line-height: 19px;
    text-align: center;
    padding-top: 12px;
  }
  .contact__row { display: flex; justify-content: center; align-items: center; gap: 8px; }
  .contact__item { display: inline-flex; align-items: center; gap: 4px; }
  .contact__icon { width: 13px; height: 13px; fill: var(--sun); }

  .back-mark {
    position: absolute;
    top: 58px; left: 0; right: 0;
    text-align: center;
    color: var(--sun);
    font-family: "Open Sans", Arial, sans-serif;
    font-weight: 600;
  }
  .back-mark__circle {
    display: block;
    width: 150px; height: 150px;
    border-radius: 50%;
    background: var(--sun);
    margin: 0 auto 18px;
  }
  .back-mark__name { font-size: 26px; letter-spacing: 2px; }
  .back-url {
    position: absolute;
    top: 294px; left: 0; right: 0;
    text-align: center;
    color: var(--ink);
    font-size: 14px;
    letter-spacing: 3.2px;
  }
</style>
</head>
<body>
  <section class="card card--front">
    <header class="brand">
      <span class="brand__mark"></span>
      <div class="brand__name">maplebrook</div>
      <div class="brand__tag">pediatric dentistry</div>
    </header>
    <div class="doctors">
      <p>Mei-Ran Tsai, DMD</p>
      <p>Corinne Walbeck, DMD</p>
    </div>
    <div class="contact">
      <div class="contact__row">
        <span class="contact__item">
          <svg class="contact__icon" viewBox="0 0 24 24" aria-hidden="true"><path d="M6.6 10.8a15.1 15.1 0 0 0 6.6 6.6l2.2-2.2a1 1 0 0 1 1-.25 11.4 11.4 0 0 0 3.6.57 1 1 0 0 1 1 1V20a1 1 0 0 1-1 1A17 17 0 0 1 3 4a1 1 0 0 1 1-1h3.5a1 1 0 0 1 1 1c0 1.25.2 2.45.57 3.57a1 1 0 0 1-.25 1z"/></svg>
          555.010.0193
        </span>
        <span class="contact__item">
          <svg class="contact__icon" viewBox="0 0 24 24" aria-hidden="true"><circle cx="12" cy="12" r="11"/></svg>
          maplebrookkidsdental.example
        </span>
      </div>
      <p>Maplebrook Pediatric Dentistry, 482 Quarry Lane</p>
      <p>Suite 517, Fernhollow, ST 00412</p>
    </div>
  </section>

  <section class="card card--back">
    <div class="back-mark">
      <span class="back-mark__circle"></span>
      <div class="back-mark__name">maplebrook</div>
    </div>
    <p class="back-url">www.maplebrookkidsdental.example</p>
  </section>
</body>
</html>
```